Veldmark Supplies Business Card

Professional business card that stand out to our potential customers. Front and back with clean modern design

Industry/Entity Type

Oil and gas

Contact Information for Business Card

Name, address, website , office phone and cell number

Requirements
Must have
• Editable files for each employee

```html
<!DOCTYPE html>
<html lang="en">
<head>
<meta charset="utf-8">
<title>Veldmark Supplies Business Card</title>
<link rel="stylesheet" href="https://fonts.googleapis.com/css2?family=Montserrat:wght@400;800&display=swap">
<style>
  :root {
    --backdrop: #484848;
    --card: #171717;
    --red: #ec2024;
    --blue: #07b0d1;
    --white: #f2f2f2;
  }
  * { margin: 0; padding: 0; box-sizing: border-box; }
  html, body { width: 1200px; height: 801px; overflow: hidden; }
  body {
    background: var(--backdrop);
    font-family: "Montserrat", sans-serif;
    display: flex;
    align-items: center;
    justify-content: center;
    gap: 40px;
  }
  .card {
    width: 540px;
    height: 309px;
    background: var(--card);
    border: 2px solid var(--red);
    border-radius: 16px;
    position: relative;
    overflow: hidden;
  }
  /* Front */
  .card-front { display: flex; }
  .brand-side {
    width: 48%;
    display: flex;
    align-items: center;
    justify-content: center;
  }
  .divider {
    width: 2px;
    background: var(--red);
    margin: 60px 0;
  }
  .info-side {
    flex: 1;
    padding: 34px 22px 0 26px;
    color: var(--white);
  }
  .person-name {
    font-weight: 800;
    font-size: 25px;
    letter-spacing: 0.5px;
    line-height: 1;
  }
  .person-name .first { color: var(--red); }
  .person-name .last { color: var(--blue); }
  .person-title { font-size: 13px; margin-top: 6px; }
  .address { font-size: 13px; margin-top: 16px; line-height: 1.45; }
  .contacts { list-style: none; margin-top: 16px; font-size: 12px; }
  .contacts li { display: flex; align-items: center; gap: 8px; line-height: 1.5; }
  .contact-icon { width: 12px; height: 12px; flex: none; }
  /* Wordmark */
  .wordmark {
    display: flex;
    align-items: center;
    gap: 10px;
    color: var(--red);
    font-weight: 800;
    text-transform: uppercase;
    letter-spacing: 1px;
  }
  .wordmark-square { background: var(--blue); flex: none; }
  .wordmark-small { font-size: 20px; }
  .wordmark-small .wordmark-square { width: 18px; height: 18px; }
  /* Back */
  .card-back { display: flex; align-items: center; justify-content: center; }
  .wordmark-large { font-size: 32px; }
  .wordmark-large .wordmark-square { width: 28px; height: 28px; }
</style>
</head>
<body>
  <section class="card card-front" aria-label="Business card front">
    <div class="brand-side">
      <div class="wordmark wordmark-small"><span class="wordmark-square"></span>Veldmark Supplies</div>
    </div>
    <div class="divider"></div>
    <div class="info-side">
      <h1 class="person-name"><span class="first">DANIEL</span> <span class="last">HARLOW</span></h1>
      <p class="person-title">Managing Director</p>
      <p class="address">412 N.Ridgeline Suite 5<br>Marlow, Tx 79410</p>
      <ul class="contacts">
        <li>
          <svg class="contact-icon" viewBox="0 0 12 12"><path fill="#ec2024" d="M2 1h3l1 3-2 1a7 7 0 0 0 3 3l1-2 3 1v3c0 1-1 1-1 1C5 11 1 7 1 2c0 0 0-1 1-1z"/></svg>
          (555)210-0417
        </li>
        <li>
          <svg class="contact-icon" viewBox="0 0 12 12"><rect x="3" y="0.8" width="6" height="10.4" rx="1" fill="none" stroke="#ec2024" stroke-width="1.3"/><rect x="5" y="9" width="2" height="1" fill="#ec2024"/></svg>
          555 318 902
        </li>
        <li>
          <svg class="contact-icon" viewBox="0 0 12 12"><rect x="0.5" y="2" width="11" height="8" fill="#ec2024"/><path d="M0.5 2l5.5 4.5L11.5 2" fill="none" stroke="#171717" stroke-width="1"/></svg>
          sales@veldmarksupplies.com
        </li>
        <li>
          <svg class="contact-icon" viewBox="0 0 12 12"><circle cx="6" cy="6" r="5.3" fill="none" stroke="#ec2024" stroke-width="1.2"/><ellipse cx="6" cy="6" rx="2.3" ry="5.3" fill="none" stroke="#ec2024" stroke-width="1"/><path d="M0.7 6h10.6" stroke="#ec2024" stroke-width="1"/></svg>
          www.veldmarksupplies.com
        </li>
      </ul>
    </div>
  </section>

  <section class="card card-back" aria-label="Business card back">
    <div class="wordmark wordmark-large"><span class="wordmark-square"></span>Veldmark Supplies</div>
  </section>
</body>
</html>
```